Shopify landing page redesign for the Tidewell Pillow

I am looking for someone with Shopify experience who can redesign our desktop and mobile landing page for the Tidewell Pillow. I am attaching my vision of what I think would convince visitors to purchase. The design should be highly focused on features and benefits and it needs to show how it solves our customer’s sleeping problems. It should also be designed with minimal distractions. Blue color is RGB: 0, 176, 24 or HEX: #00B0F0 I am looking for fast delivery.

```html
<!DOCTYPE html>
<html lang="en">
<head>
<meta charset="utf-8">
<title>Tidewell Pillow – Adjust It. Fluff It. Love It.</title>
<link href="https://fonts.googleapis.com/css2?family=Lexend:wght@300;400;500;600&family=Great+Vibes&display=swap" rel="stylesheet">
<style>
:root{
  --blue:#1f80d8;
  --blue-dark:#1466b4;
  --ink:#161a22;
  --body:#4a4f5a;
  --grey:#f2f3f5;
  --line:#e3e7ee;
  --gold:#f6b82a;
  --white:#ffffff;
}
*{box-sizing:border-box;margin:0;padding:0}
html,body{width:1200px;height:3967px;overflow:hidden}
body{position:relative;background:var(--white);font-family:"Lexend",sans-serif;color:var(--ink)}
.abs{position:absolute}
.script{font-family:"Great Vibes",cursive;color:var(--blue);font-weight:400;text-transform:none}
.wordmark{font-family:"Lexend",sans-serif;font-weight:600;color:var(--blue);letter-spacing:.5px;display:flex;align-items:center;gap:10px}
.wordmark .dot{width:14px;height:14px;border-radius:50%;background:var(--blue)}
.btn{position:absolute;display:flex;align-items:center;justify-content:center;background:var(--blue);color:#fff;border-radius:20px;font-size:13px;font-weight:500;letter-spacing:.3px;box-shadow:2px 3px 0 var(--ink);text-transform:uppercase}
.placeholder{position:absolute}
/* header */
.site-header{position:absolute;top:0;left:0;width:1200px;height:77px;background:#fff}
/* hero */
.hero-title{left:111px;top:160px;font-size:33px;font-weight:500;letter-spacing:.3px}
.hero-title .script{font-size:44px}
.hero-sub{left:111px;top:222px;width:420px;font-size:15px;line-height:37px;color:var(--ink)}
.hero-note{left:130px;top:375px;font-size:10px;font-weight:500;color:#333}
.review-card{left:136px;top:428px;width:346px;height:114px;background:#fff;border:1px solid var(--line);border-radius:12px;box-shadow:0 4px 16px rgba(0,0,0,.06)}
.stars{color:var(--gold);font-size:20px;letter-spacing:3px}
/* features ring */
.feat-label{font-size:17px;font-weight:500;line-height:32px}
.icon-circle{position:absolute;border-radius:50%;background:var(--blue);display:flex;align-items:center;justify-content:center;box-shadow:0 0 0 4px #fff,0 0 0 5px #cfe3f6}
/* designed section */
.grey-band{left:0;top:1463px;width:1200px;height:962px;background:var(--grey)}
.designed-panel{left:599px;top:1270px;width:490px;height:466px;background:var(--blue);color:#fff}
.designed-panel h2{position:absolute;left:34px;top:50px;font-size:28px;font-weight:500;line-height:58px;width:420px}
.designed-panel .script{color:#fff;font-size:40px}
.bullets{position:absolute;left:34px;top:178px;list-style:none;font-size:15px;font-weight:300}
.bullets li{display:flex;gap:14px;margin-bottom:21px;line-height:30px;align-items:flex-start}
.bullets li svg{flex:none;margin-top:9px}
/* cards */
.section-title{width:1200px;text-align:center;font-size:28px;font-weight:500}
.section-title .script{font-size:38px}
.card{position:absolute;background:#fff;border:1px solid var(--line);border-radius:12px;box-shadow:0 3px 12px rgba(0,0,0,.05);text-align:center}
.card h3{font-size:18px;font-weight:500;text-transform:uppercase}
.card p{font-size:13px;line-height:31px;color:var(--body);font-weight:300}
.card.blue{background:var(--blue);color:#fff;border-color:var(--blue)}
.card.blue p{color:#fff}
.card .ic{width:76px;height:76px;border-radius:50%;background:var(--blue);margin:0 auto;display:flex;align-items:center;justify-content:center}
.card.blue .ic{background:#fff}
/* testimonial */
.arrow{position:absolute;width:30px;height:30px;border:2px solid var(--ink);border-radius:50%;display:flex;align-items:center;justify-content:center}
.quote-text{left:553px;top:2665px;width:380px;font-size:16px;line-height:36px}
/* guarantees */
.g-card h3{font-size:18px;font-weight:500}
/* footer */
.site-footer{left:0;top:3816px;width:1200px;height:151px;background:var(--grey)}
.social{position:absolute;top:3856px;width:28px;height:28px;border:2px solid var(--ink);border-radius:50%}
</style>
</head>
<body>

<!-- Header -->
<header class="site-header">
  <div class="abs wordmark" style="left:111px;top:30px;font-size:28px"><span class="dot"></span>Tidewell</div>
  <div class="btn" style="left:973px;top:22px;width:115px;height:34px">Buy Now</div>
</header>

<!-- Hero -->
<section class="hero">
  <svg class="abs" style="left:0;top:77px" width="1200" height="610" viewBox="0 0 1200 610" role="img" aria-label="Smiling woman sitting on white bedding hugging a quilted white pillow with blue piping">
    <defs>
      <linearGradient id="heroBg" x1="0" y1="0" x2="1" y2="1">
        <stop offset="0" stop-color="#eef0f3"/>
        <stop offset=".55" stop-color="#f7f7f8"/>
        <stop offset="1" stop-color="#dfe2e6"/>
      </linearGradient>
    </defs>
    <path d="M0 0H1200V470C900 640 300 640 0 470Z" fill="url(#heroBg)"/>
    <path d="M0 470C300 630 900 630 1200 470" fill="none" stroke="var(--blue)" stroke-width="14"/>
  </svg>
  <h1 class="abs hero-title">ADJUST IT. <span class="script">Fluff it.</span> LOVE IT.</h1>
  <p class="abs hero-sub">Shop the adjustable Tidewell Pillow and get the best sleep of your life!</p>
  <div class="btn" style="left:111px;top:320px;width:226px;height:34px">Try it now &amp; get $20 off</div>
  <p class="abs hero-note">90-DAY MONEY BACK GUARANTEE</p>
  <div class="abs review-card">
    <div class="abs stars" style="left:20px;top:24px">★★★★★</div>
    <div class="abs" style="left:20px;top:66px;font-size:14px">"Best sleep I've ever had!"</div>
    <div class="abs" style="right:24px;top:48px;font-size:13px;font-weight:500;color:var(--blue)">MAYA L.</div>
  </div>
</section>

<!-- Feature ring -->
<section class="feature-ring">
  <div class="placeholder" role="img" aria-label="Open white pillow spilling blue shredded memory foam fill" style="left:15px;top:662px;width:416px;height:262px;border-radius:46% 40% 44% 40%;background:radial-gradient(ellipse at 35% 65%,#a9d8f2 0,#e9eef3 40%,#f6f7f9 70%,#fff 100%)"></div>
  <svg class="abs" style="left:0;top:690px" width="1200" height="540" viewBox="0 690 1200 540">
    <path d="M383 1100C370 930 480 840 617 849C760 858 850 960 849 1035C848 1080 830 1120 805 1155" fill="none" stroke="var(--blue)" stroke-width="1.4" stroke-dasharray="4 4"/>
  </svg>
  <div class="abs feat-label" style="left:524px;top:771px">3-YEAR WARRANTY</div>
  <div class="icon-circle" style="left:586px;top:818px;width:62px;height:62px">
    <svg width="30" height="30" viewBox="0 0 30 30" fill="none" stroke="#fff" stroke-width="2"><path d="M15 3L25 7V14C25 20 20 25 15 27C10 25 5 20 5 14V7Z"/><path d="M10 15L14 19L20 11"/></svg>
  </div>
  <div class="abs feat-label" style="left:169px;top:993px">FREE SHIPPING</div>
  <div class="icon-circle" style="left:329px;top:979px;width:62px;height:62px">
    <svg width="30" height="30" viewBox="0 0 30 30" fill="none" stroke="#fff" stroke-width="2"><path d="M5 10L15 5L25 10V21L15 26L5 21Z"/><path d="M5 10L15 15L25 10M15 15V26"/></svg>
  </div>
  <div class="icon-circle" style="left:818px;top:1004px;width:62px;height:62px">
    <svg width="30" height="30" viewBox="0 0 30 30" fill="none" stroke="#fff" stroke-width="2"><circle cx="15" cy="16" r="10"/><path d="M15 10V16L19 19M11 3H19"/></svg>
  </div>
  <div class="abs feat-label" style="left:910px;top:1002px">90-NIGHT<br>FREE TRIAL</div>
  <div class="abs" style="left:420px;top:1040px;width:360px;text-align:center;color:var(--blue)">
    <div style="font-size:64px;font-weight:600;line-height:70px">Tidewell</div>
    <div style="font-size:28px;font-weight:600;letter-spacing:10px">PILLOW</div>
  </div>
</section>

<!-- Designed for the sleep -->
<div class="abs grey-band"></div>
<section class="designed">
  <div class="placeholder" role="img" aria-label="Woman in white pajamas sleeping peacefully on a quilted white pillow" style="left:111px;top:1270px;width:488px;height:466px;background:linear-gradient(135deg,#6d7a6a 0%,#c9c3bb 30%,#eceae7 60%,#f7f7f7 100%)"></div>
  <div class="abs designed-panel">
    <h2>DESIGNED FOR THE <span class="script">Sleep You Deserve!</span></h2>
    <ul class="bullets">
      <li><svg width="16" height="12" viewBox="0 0 16 12"><path d="M1 3L15 1V11L1 9Z" fill="#fff"/></svg>Fully adjustable for all sleep positions</li>
      <li><svg width="16" height="12" viewBox="0 0 16 12"><path d="M1 3L15 1V11L1 9Z" fill="#fff"/></svg>Memory foam blend relieves neck pain</li>
      <li><svg width="16" height="12" viewBox="0 0 16 12"><path d="M1 3L15 1V11L1 9Z" fill="#fff"/></svg>Maintains shape - no more flipping</li>
      <li><svg width="16" height="12" viewBox="0 0 16 12"><path d="M1 3L15 1V11L1 9Z" fill="#fff"/></svg>Stay cool with CoolWeave Technology™</li>
      <li><svg width="16" height="12" viewBox="0 0 16 12"><path d="M1 3L15 1V11L1 9Z" fill="#fff"/></svg>Soft hypoallergenic cover for<br>sensitive skin</li>
    </ul>
  </div>
  <div class="placeholder" role="img" aria-label="Two stacked white quilted pillows with blue piping" style="left:916px;top:1625px;width:231px;height:143px;border-radius:40%;background:radial-gradient(ellipse,#ffffff 0,#eef1f4 60%,rgba(238,241,244,0) 72%)"></div>
</section>

<!-- Perfect pillow -->
<section class="perfect">
  <h2 class="abs section-title" style="left:0;top:1815px">THE PERFECT PILLOW FOR A <span class="script">Better Night's Sleep</span></h2>
  <div class="card" style="left:111px;top:1925px;width:316px;height:418px">
    <div class="ic" style="margin-top:28px"><svg width="38" height="38" viewBox="0 0 38 38" fill="none" stroke="#fff" stroke-width="2"><path d="M10 6C14 12 14 26 10 32H28C24 26 24 12 28 6Z"/><path d="M4 19H9M6 16L9 19L6 22M34 19H29M32 16L29 19L32 22"/></svg></div>
    <h3 style="margin-top:28px">Adjustable for all sleepers</h3>
    <p style="margin:18px 16px 0">Everyone sleeps differently, so why should you settle for a one size-fits-all pillow? With the Tidewell Pillow you can add or remove filling to customize the pillow's height and firmness to match your sleep style - perfect for side, back, and stomach sleepers.</p>
  </div>
  <div class="card blue" style="left:444px;top:1925px;width:316px;height:418px">
    <div class="ic" style="margin-top:28px"><svg width="38" height="38" viewBox="0 0 38 38" fill="none" stroke="var(--blue)" stroke-width="2"><path d="M6 16L19 10L32 16L19 22Z"/><path d="M6 21L19 27L32 21M6 26L19 32L32 26"/></svg></div>
    <h3 style="margin-top:28px">Cloudlike comfort</h3>
    <p style="margin:18px 16px 0">Engineered to deliver better sleep with TIDE comfort Fill, a special blend of gel-infused memory foam and microfiber clusters. Cradles your head, neck and shoulders to help relieve pressure points that cause pain. Maintains its shape - never goes flat.</p>
  </div>
  <div class="card" style="left:779px;top:1913px;width:316px;height:209px;text-align:center">
    <div class="ic abs" style="left:54px;top:14px;width:62px;height:62px"><svg width="32" height="32" viewBox="0 0 32 32" fill="none" stroke="#fff" stroke-width="2"><circle cx="16" cy="16" r="11"/><path d="M16 8V24M9 12L23 20M23 12L9 20"/></svg></div>
    <h3 class="abs" style="left:142px;top:34px;font-size:17px">Stay cooler</h3>
    <p class="abs" style="left:12px;top:88px;width:292px;line-height:28px">Designed to keep you cooler with CoolWeave Technology. Featuring temperature regulating materials that draws heat away from your body - keeping you comfortably cool all night.</p>
  </div>
  <div class="card" style="left:779px;top:2145px;width:316px;height:208px">
    <div class="ic abs" style="left:54px;top:14px;width:62px;height:62px"><svg width="32" height="32" viewBox="0 0 32 32" fill="none" stroke="#fff" stroke-width="2"><circle cx="12" cy="12" r="4"/><circle cx="21" cy="11" r="3"/><circle cx="14" cy="21" r="4"/><circle cx="22" cy="20" r="2.5"/></svg></div>
    <h3 class="abs" style="left:142px;top:22px;font-size:16px;text-align:left;line-height:31px">Sensitive skin<br>safe</h3>
    <p class="abs" style="left:10px;top:88px;width:296px;line-height:28px">Hypoallergenic bamboo rayon cover is perfect for sensitive skin. Softer than silk and cooler than cotton, ensuring you an allergy free restful night's sleep. Machine wash to keep it fresh.</p>
  </div>
</section>

<!-- Testimonials -->
<section class="testimonials">
  <div class="placeholder" role="img" aria-label="Corner of a quilted white pillow with blue piping" style="left:0;top:2425px;width:262px;height:193px;background:linear-gradient(160deg,#f2f4f6 0%,#fbfbfc 70%,rgba(255,255,255,0) 100%);border-bottom:5px solid #5aa9ec;border-radius:0 0 60% 0"></div>
  <h2 class="abs section-title" style="left:0;top:2503px">WHAT OUR CUSTOMER <span class="script">are saying...</span></h2>
  <div class="arrow" style="left:134px;top:2702px"><svg width="14" height="14" viewBox="0 0 14 14" fill="none" stroke="var(--ink)" stroke-width="2"><path d="M12 7H2M6 3L2 7L6 11"/></svg></div>
  <div class="arrow" style="left:1032px;top:2702px"><svg width="14" height="14" viewBox="0 0 14 14" fill="none" stroke="var(--ink)" stroke-width="2"><path d="M2 7H12M8 3L12 7L8 11"/></svg></div>
  <div class="abs" style="left:272px;top:2580px;font-size:90px;color:#9cc8ef;font-family:Georgia,serif;line-height:1">“</div>
  <div class="placeholder" role="img" aria-label="Portrait of a smiling customer with arms crossed" style="left:274px;top:2623px;width:188px;height:188px;border-radius:50%;background:radial-gradient(circle at 50% 40%,#e7f1fa 0,#bcdcf3 100%)"></div>
  <div class="abs stars" style="left:553px;top:2620px">★★★★★</div>
  <p class="abs quote-text">I'm in love with this pillow! Since I started using it, my sleep has been incredibly restful. It's like sleeping on a fluffy cloud!</p>
  <div class="abs" style="left:553px;top:2792px;font-size:16px;font-weight:500;color:var(--blue)">- JENNA R.</div>
</section>

<!-- Guarantees -->
<section class="guarantees">
  <div class="placeholder" role="img" aria-label="Blonde woman sleeping on soft white bedding" style="left:0;top:2903px;width:1200px;height:374px;background:linear-gradient(100deg,#d8d2cb 0%,#efece8 35%,#fafafa 60%,#ffffff 100%)"></div>
  <div class="abs" style="left:780px;top:3040px;width:300px;text-align:center;color:var(--blue)">
    <div style="font-size:54px;font-weight:600;line-height:60px">Tidewell</div>
    <div style="font-size:24px;font-weight:600;letter-spacing:9px">PILLOW</div>
  </div>
  <div class="card g-card" style="left:177px;top:3214px;width:391px;height:356px">
    <div class="icon-circle" style="left:158px;top:26px;width:74px;height:74px;box-shadow:none"><svg width="38" height="38" viewBox="0 0 38 38" fill="none" stroke="#fff" stroke-width="2"><circle cx="19" cy="16" r="10"/><path d="M14 16L18 20L24 12M12 25L8 34L13 32L15 36L19 27M26 25L30 34L25 32L23 36L19 27"/></svg></div>
    <h3 class="abs" style="left:0;top:136px;width:391px">90-NIGHT RISK-FREE GUARANTEE</h3>
    <p class="abs" style="left:30px;top:178px;width:331px">Try the Tidewell Pillow at home for 90-nights, if you don't absolutely love it, you can return it for a full refund.</p>
    <div class="btn" style="left:83px;top:293px;width:225px;height:34px">Try it now &amp; get $20 off</div>
  </div>
  <div class="card g-card" style="left:631px;top:3214px;width:392px;height:356px">
    <div class="icon-circle" style="left:159px;top:69px;width:74px;height:74px;box-shadow:none"><svg width="38" height="38" viewBox="0 0 38 38" fill="none" stroke="#fff" stroke-width="2"><path d="M19 5L31 10V18C31 26 25 31 19 34C13 31 7 26 7 18V10Z"/><path d="M13 19L17 23L25 14"/></svg></div>
    <h3 class="abs" style="left:0;top:179px;width:392px">3-YEAR WARRANTY</h3>
    <p class="abs" style="left:40px;top:222px;width:312px">Sleep soundly knowing every Tidewell Pillow comes with a 3-year warranty.</p>
  </div>
</section>

<!-- CTA -->
<section class="cta">
  <h2 class="abs" style="left:111px;top:3640px;font-size:28px;font-weight:500">READY FOR THE SLEEP <span class="script" style="font-size:40px">You Deserve?</span></h2>
  <p class="abs" style="left:111px;top:3707px;font-size:16px">Ships fast. Full refund if not delighted.</p>
  <div class="btn" style="left:818px;top:3672px;width:269px;height:36px">Start sleeping better tonight</div>
</section>

<!-- Footer -->
<footer class="abs site-footer">
  <div class="abs wordmark" style="left:111px;top:50px;font-size:30px"><span class="dot"></span>Tidewell</div>
  <div class="social" style="left:961px;top:40px"></div>
  <div class="social" style="left:995px;top:40px"></div>
  <div class="social" style="left:1029px;top:40px"></div>
  <div class="social" style="left:1063px;top:40px"></div>
  <div class="abs" style="right:110px;top:99px;font-size:13px;font-weight:500">@2025 COPYRIGHTS <span style="color:var(--blue)">TIDEWELL PILLOW</span> - ALL RIGHTS RESERVED</div>
</footer>

</body>
</html>
```